Oil Field Service company needs professional business cards

Looking to clean up our current company business cards and look a little more professional. Brenwick Casing Services is a US based company that services the oil field. We deal with engineers, managers and oil rigs....................................................................................................................................................................................................................................................................................................................................................................................................

Target Market(s)

Oil and Gas professionals

Industry/Entity Type

Oil And Gas

Contact Information for Business Card

See attached photo as example

Font styles to use
Sans Serif

Colors
ec1f27

Requirements
Must have
• Company Logo, Name, Title, Cell, Office, Fax, Email.
• See attached photo
Nice to have
• External CRT, Internal CRT, Casing Crews, Torque Turn, Laydown Machine
Should not have
• Do not introduce any new pictures and keep it professional looking

```html
<!DOCTYPE html>
<html lang="en">
<head>
<meta charset="utf-8">
<title>Brenwick Casing Services – Business Card</title>
<link rel="stylesheet" href="https://fonts.googleapis.com/css2?family=Open+Sans:wght@400;600;700&family=Roboto+Condensed:wght@700&display=swap">
<style>
  :root {
    --slate: #46525c;
    --slate-dark: #3b464f;
    --red: #ec1f27;
    --ink: #55595d;
    --grey: #7a7f84;
    --paper: #ffffff;
    --backdrop: #e6e7e9;
  }
  * { box-sizing: border-box; margin: 0; padding: 0; }
  html, body {
    width: 1200px; height: 950px; overflow: hidden;
    background: var(--backdrop);
    font-family: "Open Sans", Arial, sans-serif;
  }
  .sheet {
    width: 1200px; height: 950px;
    display: flex; flex-direction: column;
    align-items: center; justify-content: center; gap: 50px;
  }
  .card {
    width: 700px; height: 400px;
    position: relative; overflow: hidden;
    box-shadow: 0 6px 18px rgba(0,0,0,.18);
  }

  /* Front */
  .card-front { background: var(--paper); }
  .name-band {
    position: absolute; left: 0; right: 0; top: 62px; height: 58px;
    background: var(--slate);
    display: flex; align-items: center; justify-content: center;
  }
  .holder-name {
    color: #fff; font-weight: 700; font-size: 34px;
    letter-spacing: 1px; text-transform: uppercase;
  }
  .holder-title {
    position: absolute; top: 132px; left: 0; right: 0; text-align: center;
    color: var(--grey); font-size: 20px; letter-spacing: 3px;
  }
  .contact {
    position: absolute; top: 186px; left: 0; right: 0;
    text-align: center; color: var(--ink); font-size: 17px; line-height: 31px;
  }
  .contact .label { color: var(--red); font-weight: 700; }
  .contact .cell { font-weight: 700; color: #3d4144; }
  .services {
    position: absolute; bottom: 26px; left: 0; right: 0;
    text-align: center;
    font-family: "Roboto Condensed", "Arial Narrow", sans-serif;
    font-weight: 700; font-size: 15px; color: var(--ink);
    text-transform: uppercase; letter-spacing: .3px;
  }
  .services .sep { color: var(--red); margin: 0 7px; }

  /* Back */
  .card-back {
    background: var(--slate);
    display: flex; flex-direction: column; align-items: center; justify-content: center;
    color: #fff; font-weight: 700;
  }
  .brand-name { font-size: 78px; letter-spacing: 2px; line-height: 1; text-transform: uppercase; }
  .brand-line { font-size: 20px; letter-spacing: 9px; margin-top: 16px; text-transform: uppercase; }
</style>
</head>
<body>
<main class="sheet">
  <section class="card card-front" aria-label="Business card front">
    <div class="name-band"><h1 class="holder-name">Cody Harlan</h1></div>
    <p class="holder-title">AREA MANAGER</p>
    <address class="contact">
      <div><span class="label">A:</span> Alden, OK 73000</div>
      <div><span class="label">P:</span> (555)210-4400 <span class="label">C:</span> <span class="cell">(555)318-6021</span> <span class="label">F:</span> (555)210-4411</div>
      <div><span class="label">E:</span> cody@brenwick.com <span class="label">W:</span> www.brenwick.com</div>
    </address>
    <p class="services">
      External CRT<span class="sep">|</span>Internal CRT<span class="sep">|</span>Casing Crews<span class="sep">|</span>Torque Turn<span class="sep">|</span>Laydown Machine
    </p>
  </section>

  <section class="card card-back" aria-label="Business card back">
    <div class="brand-name">Brenwick</div>
    <div class="brand-line">Casing Services</div>
  </section>
</main>
</body>
</html>
```